Redesign of business card for Cedar Ridge Mechanical

We are looking for a new design for our business cards for Cedar Ridge Mechanical. We are a plumbing & HVAC construction company, operating on the West Coast of Canada and USA. Logo attached.
Industry/Entity Type
Construction - Plumbing & HVAC
Contact Information for Business Card
Name, address, phone numbers, email, website address
Look and feel
Each slider illustrates characteristics of the customer's brand and the style your logo design should communicate.

```html
<!DOCTYPE html>
<html lang="en">
<head>
<meta charset="utf-8">
<title>Cedar Ridge Mechanical – Business Card</title>
<link href="https://fonts.googleapis.com/css2?family=Roboto:wght@400;700&family=Roboto+Condensed:wght@700&display=swap" rel="stylesheet">
<style>
  :root {
    --backdrop: #e9e4dc;
    --card-top: #f1f1ef;
    --card-bottom: #dcdcd9;
    --card-edge: #b9b9b6;
    --ink: #111111;
    --ink-soft: #3a3a3a;
  }
  * { margin: 0; padding: 0; box-sizing: border-box; }
  html, body {
    width: 1170px;
    height: 1200px;
    overflow: hidden;
    background: var(--backdrop);
  }
  .business-card {
    position: absolute;
    left: 70px;
    top: 305px;
    width: 1030px;
    height: 590px;
    border-radius: 30px;
    border: 2px solid var(--card-edge);
    background: linear-gradient(180deg, var(--card-top), var(--card-bottom));
    font-family: "Roboto", Arial, sans-serif;
    color: var(--ink-soft);
  }
  .person-name {
    position: absolute;
    left: 48px;
    top: 78px;
    font-family: "Roboto Condensed", "Arial Narrow", sans-serif;
    font-weight: 700;
    font-size: 40px;
    line-height: 1;
    color: var(--ink);
  }
  .person-title {
    position: absolute;
    left: 50px;
    top: 124px;
    font-size: 25px;
    line-height: 1;
  }
  .postal-address {
    position: absolute;
    left: 48px;
    top: 308px;
    font-size: 25px;
    line-height: 33px;
    font-style: normal;
  }
  .contact-list {
    position: absolute;
    left: 48px;
    top: 406px;
    list-style: none;
    font-size: 25px;
    line-height: 33px;
  }
  .contact-list li {
    display: flex;
    align-items: center;
    gap: 12px;
  }
  .contact-icon {
    width: 22px;
    height: 22px;
    flex: none;
    fill: var(--ink);
  }
  .company-mark {
    position: absolute;
    left: 430px;
    top: 150px;
    width: 560px;
    display: flex;
    align-items: center;
    gap: 26px;
  }
  .company-mark-square {
    width: 90px;
    height: 90px;
    flex: none;
    background: var(--ink);
  }
  .company-name {
    font-family: "Roboto", Arial, sans-serif;
    font-weight: 700;
    font-size: 62px;
    line-height: 1.05;
    color: var(--ink);
  }
</style>
</head>
<body>
  <section class="business-card">
    <h1 class="person-name">Daniel Harper</h1>
    <p class="person-title">President</p>

    <address class="postal-address">
      4127 Alder Crest Road<br>
      Maple Falls, WA 98266
    </address>

    <ul class="contact-list">
      <li>
        <svg class="contact-icon" viewBox="0 0 24 24" aria-hidden="true">
          <path d="M6.6 10.8c1.4 2.8 3.8 5.1 6.6 6.6l2.2-2.2c.3-.3.7-.4 1-.2 1.1.4 2.3.6 3.6.6.6 0 1 .4 1 1V20c0 .6-.4 1-1 1C10.6 21 3 13.4 3 4c0-.6.4-1 1-1h3.5c.6 0 1 .4 1 1 0 1.3.2 2.5.6 3.6.1.3 0 .7-.2 1L6.6 10.8z"/>
        </svg>
        <span>(555) 2816-4730</span>
      </li>
      <li>
        <svg class="contact-icon" viewBox="0 0 24 24" aria-hidden="true">
          <path d="M2 6h20v12H2z" fill="none"/>
          <path d="M2 7l10 6 10-6v11H2z"/>
          <path d="M2 5h20v1.2l-10 6-10-6z"/>
        </svg>
        <span>name@cedarridgemechanical.com</span>
      </li>
      <li>
        <svg class="contact-icon" viewBox="0 0 24 24" aria-hidden="true">
          <circle cx="12" cy="12" r="10"/>
          <path d="M7 7c2 0 3 1 3 3s-2 2-2 4 1 3 1 4M14 4c0 2 2 2 3 3s0 3 2 4" stroke="#e6e6e4" stroke-width="1.6" fill="none"/>
        </svg>
        <span>www.cedarridgemechanical.com</span>
      </li>
    </ul>

    <div class="company-mark">
      <span class="company-mark-square" aria-hidden="true"></span>
      <p class="company-name">Cedar Ridge<br>Mechanical</p>
    </div>
  </section>
</body>
</html>
```